Silver Bloom Marisol's Cleaning Service Business Cards Project

A business card with all contact details with logo design on there (already have a logo) eye catching Logo and contact info on one side, full logo on the back, must target upper class residential and corporate companies, fitness companies, still keep it on the feminine side of things , must look elegant

Target Market(s)

Upper class homes and corporate companies

Industry/Entity Type

Cleaning Service

Contact Information for Business Card

Name: Marisol Quenby
Position: Director
ABN: 31647209853
Email: marisolssilvercleaning@tidymail.example
Number: 0417906354

Font styles to use
Decorative

Colors

Designer to choose colors to be used in the design.

Requirements
Must have
• Available Sydney Wide, contact info and logo on one side, full logo on the back
Nice to have
• Professional appearance
Should not have
• Cheap advert looking stuff

```html
<!DOCTYPE html>
<html lang="en">
<head>
<meta charset="utf-8">
<title>Silver Bloom – Business Cards</title>
<link rel="stylesheet" href="https://fonts.googleapis.com/css2?family=Arvo:wght@400;700&family=Tinos&family=Montserrat:wght@600&display=swap">
<style>
  :root {
    --backdrop: #2b2c30;
    --card: #2d323f;
    --accent: #34dccb;
    --accent-soft: #7ff0e2;
    --ink: #ffffff;
  }
  * { margin: 0; padding: 0; box-sizing: border-box; }
  html, body {
    width: 1200px; height: 960px; overflow: hidden;
    background: var(--backdrop);
  }
  .canvas { position: relative; width: 1200px; height: 960px; }
  .card {
    position: absolute;
    width: 598px; height: 342px;
    background: var(--card);
    box-shadow: 0 3px 10px rgba(0,0,0,.55);
    text-align: center;
    color: var(--ink);
  }
  .card--front { left: 322px; top: 108px; }
  .card--back  { left: 321px; top: 493px; }

  .mark-circle {
    position: absolute; left: 50%; transform: translateX(-50%);
    border: 2px solid var(--accent); border-radius: 50%;
  }
  .card--front .mark-circle { top: 52px; width: 38px; height: 38px; }
  .wordmark-small {
    position: absolute; left: 0; right: 0; top: 96px;
    font: 400 10px/1 "Arvo", serif; letter-spacing: 2px;
    color: var(--accent);
  }
  .holder-name {
    position: absolute; left: 0; right: 0; top: 119px;
    font: 400 19px/1 "Arvo", serif; color: var(--accent);
  }
  .holder-role {
    position: absolute; left: 0; right: 0; top: 144px;
    font: 400 14px/1 "Arvo", serif; letter-spacing: .5px; color: var(--accent-soft);
  }
  .contact {
    position: absolute; left: 0; right: 0; top: 174px;
    font: 400 14px/19px "Tinos", serif; color: var(--ink);
  }
  .contact .abn { margin-bottom: 8px; }
  .divider-ornament {
    position: absolute; left: 247px; top: 268px;
    width: 104px; height: 22px;
    background: radial-gradient(ellipse at center, rgba(52,220,203,.32) 0%, rgba(52,220,203,.12) 45%, rgba(52,220,203,0) 72%);
  }
  .coverage {
    position: absolute; left: 0; right: 0; top: 302px;
    font: 600 8px/1 "Montserrat", sans-serif; letter-spacing: 3px;
    color: var(--accent-soft);
  }

  .card--back .mark-circle { top: 76px; width: 78px; height: 78px; }
  .flourish {
    position: absolute; left: 180px; top: 156px;
    width: 228px; height: 44px;
    background: radial-gradient(ellipse at center, rgba(127,240,226,.3) 0%, rgba(127,240,226,.12) 50%, rgba(127,240,226,0) 74%);
  }
  .brand-name {
    position: absolute; left: 0; right: 0; top: 208px;
    font: 400 24px/1 "Arvo", serif; letter-spacing: 1px; color: var(--accent);
  }
  .brand-tagline {
    position: absolute; left: 0; right: 0; top: 239px;
    font: 600 9px/1 "Montserrat", sans-serif; letter-spacing: 3px; color: var(--ink);
  }
</style>
</head>
<body>
<main class="canvas">
  <section class="card card--front">
    <div class="mark-circle"></div>
    <div class="wordmark-small">SILVER BLOOM</div>
    <h1 class="holder-name">MARISOL QUENBY</h1>
    <p class="holder-role">DIRECTOR</p>
    <div class="contact">
      <p class="abn">ABN: 31647209853</p>
      <p>PH: 0417906354</p>
      <p>marisolssilvercleaning@tidymail.example</p>
      <p>www.silverbloomcleaning.example</p>
    </div>
    <div class="divider-ornament" role="img" aria-label="Small decorative scroll flourish"></div>
    <p class="coverage">AVAILABLE SYDNEY WIDE</p>
  </section>

  <section class="card card--back">
    <div class="mark-circle"></div>
    <div class="flourish" role="img" aria-label="Ornamental swirling floral flourish"></div>
    <h2 class="brand-name">SILVER BLOOM</h2>
    <p class="brand-tagline">MARISOL’S CLEANING SERVICES</p>
  </section>
</main>
</body>
</html>
```